Korvath Tours in Israel business card

I am a Korvath Tours in Israel (the holy land). Prior to it I have over 20 years high-tech business. My main (but not only) focus is working with business people that come to Israel and want to get a tour (usually short from few hours to 2 days). During my guiding I incorporate a lot of my know how of the Israeli business culture. I like to have a business card that I can present to anyone that is looking for a Korvath Tours, but that business people will understand the additional value I can provide them during my tour.

Target Market(s)

Business visitors and tourist to Israel

Industry/Entity Type

Tourism

Contact Information for Business Card

Danny Korvath
email: danny@korvath-tours.example
Mobile: +972-52-7416205

Colors

Designer to choose colors to be used in the design.

Requirements
Must have
• Korvath Tours
Nice to have
• I don't know how but it should project my understanding in business not just the tourist side of my knowledge.

```html
<!DOCTYPE html>
<html lang="en">
<head>
<meta charset="utf-8">
<title>Korvath Tours – Business Card</title>
<link href="https://fonts.googleapis.com/css2?family=Poppins:wght@400;500;600&display=swap" rel="stylesheet">
<style>
  :root {
    --bg: #e6e7e9;
    --card-white: #ffffff;
    --card-grey: #6d6e72;
    --brand-blue: #2478bd;
    --wave-grey: #6a6b6f;
    --text-grey: #6b6b6b;
    --back-text: #d4d5d8;
  }
  * { box-sizing: border-box; margin: 0; padding: 0; }
  html, body { width: 1200px; height: 900px; overflow: hidden; }
  body {
    background: var(--bg);
    font-family: "Poppins", sans-serif;
    position: relative;
  }
  .card {
    position: absolute;
    width: 560px;
    height: 320px;
    border-radius: 18px;
    overflow: hidden;
    box-shadow: 0 10px 30px rgba(0,0,0,0.18);
  }
  .card-back {
    left: 520px;
    top: 70px;
    background: var(--card-grey);
    display: flex;
    align-items: center;
    justify-content: center;
  }
  .brand-name {
    font-weight: 400;
    white-space: nowrap;
  }
  .card-back .brand-name {
    font-size: 32px;
    color: var(--back-text);
  }
  .card-front {
    left: 140px;
    top: 500px;
    background: var(--card-white);
  }
  .card-front .waves {
    position: absolute;
    inset: 0;
    width: 100%;
    height: 100%;
  }
  .brand {
    position: absolute;
    left: 28px;
    top: 84px;
    width: 200px;
    display: flex;
    align-items: center;
    justify-content: center;
    gap: 10px;
  }
  .brand .brand-dot {
    width: 14px; height: 14px;
    border-radius: 50%;
    background: var(--brand-blue);
    flex: none;
  }
  .brand .brand-name {
    font-size: 21px;
    color: var(--text-grey);
  }
  .divider {
    position: absolute;
    left: 244px;
    top: 56px;
    width: 2px;
    height: 100px;
    background: var(--brand-blue);
  }
  .contact {
    position: absolute;
    left: 274px;
    top: 66px;
  }
  .contact .person-name {
    font-size: 24px;
    font-weight: 600;
    color: var(--brand-blue);
    text-transform: uppercase;
    line-height: 1.1;
  }
  .contact .person-role {
    font-size: 12px;
    font-weight: 500;
    color: var(--text-grey);
    letter-spacing: 1px;
    text-transform: uppercase;
    margin: 2px 0 10px;
  }
  .contact .line {
    display: flex;
    align-items: center;
    gap: 10px;
    font-size: 15px;
    color: var(--text-grey);
    line-height: 1.6;
    white-space: nowrap;
  }
  .contact .line svg { width: 13px; height: 13px; flex: none; }
</style>
</head>
<body>

  <section class="card card-back" aria-label="Card back">
    <span class="brand-name">Korvath Tours</span>
  </section>

  <section class="card card-front" aria-label="Card front">
    <svg class="waves" viewBox="0 0 560 320" preserveAspectRatio="none" aria-hidden="true">
      <path d="M0,150 C70,230 220,262 350,272 C440,280 500,300 525,320 L0,320 Z" fill="var(--brand-blue)"/>
      <path d="M0,168 C80,236 230,258 340,266 C430,274 490,296 515,320" fill="none" stroke="#fff" stroke-width="4"/>
      <path d="M0,176 C80,240 200,256 300,262 C390,268 460,290 490,320 L0,320 Z" fill="var(--wave-grey)"/>
      <path d="M0,200 C90,250 200,262 300,272 C390,282 450,300 470,320 L0,320 Z" fill="#fff"/>
      <path d="M0,214 C100,262 210,276 300,286 C380,294 430,308 445,320 L0,320 Z" fill="var(--brand-blue)"/>
    </svg>

    <div class="brand">
      <span class="brand-dot"></span>
      <span class="brand-name">Korvath Tours</span>
    </div>

    <div class="divider"></div>

    <div class="contact">
      <p class="person-name">Danny Korvath</p>
      <p class="person-role">Director</p>
      <p class="line">
        <svg viewBox="0 0 24 24" aria-hidden="true"><path fill="var(--brand-blue)" d="M6.6 10.8a15.1 15.1 0 0 0 6.6 6.6l2.2-2.2a1 1 0 0 1 1-.25 11.4 11.4 0 0 0 3.6.57 1 1 0 0 1 1 1V20a1 1 0 0 1-1 1A17 17 0 0 1 3 4a1 1 0 0 1 1-1h3.5a1 1 0 0 1 1 1c0 1.250.2 2.45.57 3.57a1 1 0 0 1-.25 1z"/></svg>
        +972-52-7416205
      </p>
      <p class="line">
        <svg viewBox="0 0 24 24" aria-hidden="true"><rect x="2" y="5" width="20" height="14" rx="2" fill="none" stroke="var(--brand-blue)" stroke-width="2"/><path d="M2 6l10 7 10-7" fill="none" stroke="var(--brand-blue)" stroke-width="2"/></svg>
        danny@korvath-tours.example
      </p>
    </div>
  </section>

</body>
</html>
```